Flyer / Small Safety "Poster" (A4 or 8.5x11" paper)

We're looking to create a series of safety signs for woodworkers to print on home printers using standard sized paper (A4 or 8.5x11" depending on where they are), or possibly to have printed on 17x22" paper.
Currently we want only the first one, but keep in mind that all should work together.
They need: Simple graphic. Bold Text. Company logo. Use company colors (orange, black, white.)
To begin, we will start with a single sign for hearing protection. Graphic or clip art to portray either ear plugs or ear-muff design. Text to say, "Hearing Protection is a Sound Investment."

Target Market(s)

USA Woodworkers & CNC Machinists - Male, 20-65 years old

Font styles to use
Sans Serif

Colors
f37122

Requirements
Must have
• Client logo
Nice to have
• Use client colors of black, white, & orange

```html
<!DOCTYPE html>
<html lang="en">
<head>
<meta charset="utf-8">
<title>Hearing Protection Safety Sign</title>
<link href="https://fonts.googleapis.com/css2?family=Bebas+Neue&family=Montserrat:ital,wght@0,500;0,800;1,400&display=swap" rel="stylesheet">
<style>
  :root {
    --orange: #f58025;
    --ink: #2a2a28;
    --white: #ffffff;
    --backdrop: #555555;
    --plate-tint: #fde3d0;
  }
  html, body {
    margin: 0;
    padding: 0;
    width: 1200px;
    height: 1200px;
    overflow: hidden;
    background: var(--backdrop);
  }
  .sign {
    display: block;
    width: 1200px;
    height: 1200px;
  }
  .sign-frame { fill: var(--orange); }
  .sign-face { fill: var(--white); }
  .headline-top {
    font-family: "Montserrat", sans-serif;
    font-weight: 800;
    font-size: 116px;
    fill: var(--ink);
  }
  .headline-main {
    font-family: "Bebas Neue", sans-serif;
    font-size: 158px;
    fill: var(--ink);
  }
  .tagline-band { fill: var(--orange); }
  .tagline-text {
    font-family: "Montserrat", sans-serif;
    font-weight: 500;
    font-size: 40px;
    fill: var(--white);
  }
  .warning-outer { fill: var(--orange); stroke: var(--orange); stroke-width: 44; stroke-linejoin: round; }
  .warning-gap { fill: var(--white); stroke: var(--white); stroke-width: 12; stroke-linejoin: round; }
  .warning-inner { fill: var(--orange); stroke: var(--orange); stroke-width: 10; stroke-linejoin: round; }
  .ear-plug-art { fill: var(--plate-tint); }
  .brand-name {
    font-family: "Montserrat", sans-serif;
    font-weight: 800;
    font-size: 36px;
    letter-spacing: 4px;
    fill: var(--ink);
  }
  .brand-mark { fill: var(--ink); }
  .brand-slogan {
    font-family: "Montserrat", sans-serif;
    font-style: italic;
    font-weight: 400;
    font-size: 18px;
    fill: var(--ink);
  }
</style>
</head>
<body>
<svg class="sign" viewBox="0 0 1200 1200" xmlns="http://www.w3.org/2000/svg">
  <defs>
    <radialGradient id="float-shadow" cx="50%" cy="50%" r="50%">
      <stop offset="0%" stop-color="#bdbdbd"/>
      <stop offset="100%" stop-color="#ffffff" stop-opacity="0"/>
    </radialGradient>
  </defs>

  <rect class="sign-frame" x="225" y="114" width="753" height="974" rx="28"/>
  <rect class="sign-face" x="243" y="132" width="717" height="938" rx="19"/>

  <text class="headline-top" x="321" y="248" textLength="560" lengthAdjust="spacingAndGlyphs">HEARING</text>
  <text class="headline-main" x="321" y="375" textLength="561" lengthAdjust="spacingAndGlyphs">PROTECTION</text>

  <rect class="tagline-band" x="307" y="383" width="588" height="50" rx="5"/>
  <text class="tagline-text" x="340" y="422" textLength="520" lengthAdjust="spacingAndGlyphs">IS A SOUND INVESTMENT</text>

  <polygon class="warning-outer" points="601,500 397,862 805,862"/>
  <polygon class="warning-gap" points="601,508 406,856 796,856"/>
  <polygon class="warning-inner" points="601,518 413,850 789,850"/>
  <rect class="ear-plug-art" x="528" y="660" width="150" height="150" rx="22" role="img" aria-label="Illustration of an ear with a foam ear plug being inserted"/>

  <ellipse cx="602" cy="924" rx="150" ry="14" fill="url(#float-shadow)"/>

  <rect class="brand-mark" x="376" y="970" width="30" height="30"/>
  <text class="brand-name" x="420" y="999" textLength="400" lengthAdjust="spacingAndGlyphs">BLADECRAFT SUPPLY</text>
  <text class="brand-slogan" x="830" y="1032" text-anchor="end">Sharp edges for every busy workshop!</text>
</svg>
</body>
</html>
```